Business Card Design

I already have a company logo for my company. I have a logo for the manufacturer we represent. I want a professional business card design.

```html
<!DOCTYPE html>
<html lang="en">
<head>
<meta charset="utf-8">
<title>Signalpoint Group LLC – Business Card</title>
<link rel="stylesheet" href="https://fonts.googleapis.com/css2?family=Open+Sans:wght@400;600;700;800&display=swap">
<style>
  :root {
    --bg: #202020;
    --card: #27272b;
    --card-edge: #1a1a1d;
    --red: #e4202b;
    --gold: #c8982c;
    --white: #f2f2f2;
    --soft: #d9d9d9;
    --silver: #b9b9bd;
  }
  * { margin: 0; padding: 0; box-sizing: border-box; }
  html, body {
    width: 1200px; height: 780px; overflow: hidden;
    background: var(--bg);
    font-family: "Open Sans", Arial, sans-serif;
  }
  .canvas {
    position: relative; width: 1200px; height: 780px;
    display: flex; align-items: center; justify-content: center; gap: 60px;
  }
  .card {
    position: relative; width: 520px; height: 298px;
    background: var(--card);
    border-radius: 18px; overflow: hidden;
    box-shadow: 0 18px 40px rgba(0,0,0,.55), 0 0 0 1px var(--card-edge);
  }
  .card__bands { position: absolute; inset: 0; width: 520px; height: 298px; }

  /* front */
  .brand {
    position: absolute; left: 34px; top: 112px; width: 200px;
    display: flex; align-items: center; gap: 10px;
  }
  .brand__square { width: 14px; height: 14px; background: var(--red); flex: none; }
  .brand__name {
    color: var(--white); font-weight: 800; font-size: 21px; line-height: 1.1;
    text-transform: uppercase; letter-spacing: .5px;
  }
  .contact { position: absolute; left: 262px; top: 74px; color: var(--white); }
  .contact__name { font-size: 27px; font-weight: 700; line-height: 1.1; }
  .contact__first { color: var(--red); }
  .contact__last { color: var(--gold); }
  .contact__title { font-size: 12.5px; color: var(--soft); margin-top: 2px; }
  .contact__address { font-size: 12.5px; line-height: 1.4; margin-top: 12px; }
  .contact__list { list-style: none; margin-top: 8px; font-size: 12.5px; line-height: 1.55; }
  .contact__list li { display: flex; align-items: center; gap: 7px; }
  .contact__icon { width: 12px; height: 12px; flex: none; }

  /* back */
  .card--back .brand {
    left: 0; right: 0; top: 0; bottom: 0; width: auto;
    justify-content: center; gap: 14px;
  }
  .card--back .brand__square { width: 20px; height: 20px; background: var(--silver); }
  .card--back .brand__name { color: var(--silver); font-size: 32px; }
</style>
</head>
<body>
<main class="canvas">

  <section class="card card--front" aria-label="Business card front">
    <svg class="card__bands" viewBox="0 0 520 298" aria-hidden="true">
      <polygon points="0,0 300,0 282,17 0,17" fill="var(--red)"/>
      <polygon points="230,298 248,281 520,281 520,298" fill="var(--gold)"/>
      <line x1="282" y1="44" x2="206" y2="262" stroke="var(--gold)" stroke-width="1"/>
    </svg>

    <div class="brand">
      <span class="brand__square"></span>
      <span class="brand__name">Signalpoint<br>Group LLC</span>
    </div>

    <div class="contact">
      <h1 class="contact__name"><span class="contact__first">Tomas</span> <span class="contact__last">Verhoef</span></h1>
      <p class="contact__title">Managing Director</p>
      <p class="contact__address">1840 Larkspur Ave. Suite 300<br>Denton Ridge, TX 75010</p>
      <ul class="contact__list">
        <li>
          <svg class="contact__icon" viewBox="0 0 24 24" aria-hidden="true"><path fill="var(--red)" d="M6.6 10.8a15.1 15.1 0 0 0 6.6 6.6l2.2-2.2c.3-.3.7-.4 1-.2 1.1.4 2.3.6 3.6.6.6 0 1 .4 1 1V20c0 .6-.4 1-1 1A17 17 0 0 1 3 4c0-.6.4-1 1-1h3.5c.6 0 1 .4 1 1 0 1.3.2 2.5.6 3.6.1.3 0 .7-.2 1z"/></svg>
          (555) 214-6830
        </li>
        <li>
          <svg class="contact__icon" viewBox="0 0 24 24" aria-hidden="true"><rect x="2" y="5" width="20" height="14" rx="2" fill="var(--red)"/><path d="M3 6l9 7 9-7" fill="none" stroke="var(--card)" stroke-width="2"/></svg>
          hello@signalpoint.co
        </li>
        <li>
          <svg class="contact__icon" viewBox="0 0 24 24" aria-hidden="true"><circle cx="12" cy="12" r="10" fill="var(--red)"/><path d="M2 12h20M12 2c3 3 3 17 0 20M12 2c-3 3-3 17 0 20" fill="none" stroke="var(--card)" stroke-width="1.6"/></svg>
          www.signalpoint.co
        </li>
      </ul>
    </div>
  </section>

  <section class="card card--back" aria-label="Business card back">
    <div class="brand">
      <span class="brand__square"></span>
      <span class="brand__name">Signalpoint<br>Group LLC</span>
    </div>
  </section>

</main>
</body>
</html>
```